Computer consultant business card

Zorvik Software is a newly started computer consulting company. It's a small one-man company that provides mostly Vornix applications but also websites in collaboration with designers. I'm running this company on the side of full time university studies.

I want the final design to be clean and memorable. Be creative! :)

Some inspiration:
http://www.pixelmarta.com/design/48317
http://www.pixelmarta.com/design/2739164/business-card-design-by-frostlynk
http://www.pixelmarta.com/design/604281/business-card-design-by-koralind-vestrabanu

See attachment for my company logo.
Updates

I would like to thank everyone for submitting! I'll need a couple of days to review and ultimately select a design.

Target Market(s)

Non-technical entrepreneurs and small companies.

Industry/Entity Type

University

Requirements
Must have
• My company logo.
In any way, both colors from my logo.
First- and last name, e-mail and phone number.
Double-sided design.
Nice to have
• Something creative with the symbol in my logo

```html
<!DOCTYPE html>
<html lang="en">
<head>
<meta charset="utf-8">
<title>Zorvik Software – Business Card Set</title>
<link rel="stylesheet" href="https://fonts.googleapis.com/css2?family=Source+Sans+3:wght@400;600;700&display=swap">
<style>
  :root {
    --backdrop: #b7946a;
    --label: #1e1a16;
    --card-white: #ffffff;
    --ink-dark: #2f2c2d;
    --brand-blue: #4a74bd;
    --card-black: #050505;
    --slate-top: #2e2f34;
    --slate-bottom: #4a5878;
    --white: #ffffff;
    --shadow: 0 3px 10px rgba(0, 0, 0, 0.35);
  }
  * { box-sizing: border-box; margin: 0; padding: 0; }
  html, body { width: 1200px; height: 788px; overflow: hidden; }
  body {
    position: relative;
    background: var(--backdrop);
    font-family: "Source Sans 3", Arial, sans-serif;
  }
  .card-label {
    position: absolute;
    width: 525px;
    text-align: center;
    font-size: 21px;
    color: var(--label);
  }
  .card {
    position: absolute;
    width: 525px;
    height: 299px;
    border-radius: 22px;
    box-shadow: var(--shadow);
    overflow: hidden;
  }
  .card--front  { left: 54px;  top: 75px;  background: var(--card-white); }
  .card--back-1 { left: 622px; top: 75px;  background: var(--card-white); }
  .card--back-2 { left: 54px;  top: 446px; background: var(--card-black); }
  .card--back-3 {
    left: 622px; top: 446px;
    background: radial-gradient(ellipse 80% 90% at 50% 110%, var(--slate-bottom), var(--slate-top) 75%);
  }

  .brand {
    position: absolute;
    display: flex;
    align-items: center;
  }
  .brand__dot {
    border-radius: 50%;
    background: var(--brand-blue);
    flex: none;
  }
  .brand__name {
    font-weight: 600;
    line-height: 1;
    letter-spacing: -0.5px;
  }

  /* front */
  .card--front .brand { left: 29px; top: 204px; gap: 14px; }
  .card--front .brand__dot { width: 66px; height: 66px; }
  .card--front .brand__name { font-size: 44px; color: var(--ink-dark); }
  .contact {
    position: absolute;
    left: 259px;
    top: 206px;
    color: var(--brand-blue);
  }
  .contact__name { font-size: 19px; font-weight: 700; }
  .contact__role { font-size: 13px; margin-top: 1px; }
  .contact__lines {
    display: flex; gap: 8px; align-items: center;
    margin-top: 3px; font-size: 14px; color: var(--ink-dark);
  }
  .contact__lines span { display: inline-flex; align-items: center; gap: 4px; }
  .contact__lines svg { width: 9px; height: 9px; fill: var(--ink-dark); }

  /* backs */
  .card--back-1 .brand,
  .card--back-2 .brand,
  .card--back-3 .brand {
    left: 0; right: 0; top: 88px;
    justify-content: center; gap: 24px;
  }
  .card .brand--large .brand__dot { width: 104px; height: 104px; }
  .card .brand--large .brand__name { font-size: 80px; }
  .card--back-1 .brand__name { color: var(--ink-dark); }
  .card--back-2 .brand__name,
  .card--back-3 .brand__name { color: var(--white); }

  .web {
    position: absolute;
    left: 0; right: 0; top: 247px;
    text-align: center;
    font-size: 19px;
    letter-spacing: 5px;
  }
  .card--back-1 .web { color: var(--ink-dark); }
  .card--back-2 .web,
  .card--back-3 .web { color: var(--white); }

  .texture {
    position: absolute; inset: 0;
    background:
      radial-gradient(ellipse 45% 40% at 30% 0%, rgba(120,120,120,0.45), transparent 70%),
      radial-gradient(ellipse 40% 40% at 80% 100%, rgba(150,140,140,0.45), transparent 70%);
  }
</style>
</head>
<body>

  <div class="card-label" style="left:54px; top:33px;">Front</div>
  <section class="card card--front">
    <div class="brand">
      <span class="brand__dot"></span>
      <span class="brand__name">zorvik</span>
    </div>
    <div class="contact">
      <p class="contact__name">First Name + Last Name</p>
      <p class="contact__role">Designation</p>
      <p class="contact__lines">
        <span><svg viewBox="0 0 10 10" aria-hidden="true"><path d="M2 0.5l2 2-1 1.2a6 6 0 0 0 3.3 3.3l1.2-1 2 2-1.3 1.5C5 9.5 0.5 5 1 1.8z"/></svg>+12 345 6789</span>
        <span><svg viewBox="0 0 10 10" aria-hidden="true"><path d="M0.5 2h9v6h-9z"/></svg>info@website.com</span>
      </p>
    </div>
  </section>

  <div class="card-label" style="left:622px; top:33px;">Back - 1</div>
  <section class="card card--back-1">
    <div class="brand brand--large">
      <span class="brand__dot"></span>
      <span class="brand__name">zorvik</span>
    </div>
    <p class="web">www.website.com</p>
  </section>

  <div class="card-label" style="left:54px; top:404px;">Back - 2</div>
  <section class="card card--back-2">
    <div class="texture" role="img" aria-label="Perforated metal dot texture glowing in the corners"></div>
    <div class="brand brand--large">
      <span class="brand__dot"></span>
      <span class="brand__name">zorvik</span>
    </div>
    <p class="web">www.website.com</p>
  </section>

  <div class="card-label" style="left:622px; top:404px;">Back - 3</div>
  <section class="card card--back-3">
    <div class="brand brand--large">
      <span class="brand__dot"></span>
      <span class="brand__name">zorvik</span>
    </div>
    <p class="web">www.website.com</p>
  </section>

</body>
</html>
```